professional business card design for technology company

We are a small technology consulting firm, specialising in consulting based around Cloud and Managed services. Our colour scheme is yellow, blue and white, as you can see in the logos. Although we are based in melbourne australia, due to the nature of our work, our clients can be located anywhere. We are looking for a clean, professional, positive look - similar to our company logo

Target Market(s)

small business

Industry/Entity Type

Business

Contact Information for Business Card

eye catching, designed to incorporate some level of raised printing. Must contain website address, phone number, name and job title

Requirements
Must have
• Logo (attached) - use of the same colour scheme

```html
<!DOCTYPE html>
<html lang="en">
<head>
<meta charset="utf-8">
<title>Norvale Business Card</title>
<link rel="stylesheet" href="https://fonts.googleapis.com/css2?family=Montserrat:wght@400;500;800&family=Open+Sans:wght@500;600&display=swap">
<style>
  :root {
    --blue: #2ea6da;
    --ink: #555658;
    --paper: #f1f1f1;
    --stage: #dcdcdc;
    --yellow: #f2cd12;
  }
  html, body {
    margin: 0;
    width: 1200px;
    height: 960px;
    overflow: hidden;
    background: var(--stage);
  }
  .canvas {
    position: relative;
    width: 1200px;
    height: 960px;
  }
  .card {
    position: absolute;
    left: 280px;
    width: 640px;
    height: 366px;
    background: var(--paper);
    box-shadow: 0 6px 18px rgba(0,0,0,0.18);
    overflow: hidden;
  }
  .card--front { top: 84px; }
  .card--back { top: 510px; }
  .card__bands {
    position: absolute;
    inset: 0;
  }
  .brand {
    position: absolute;
    display: flex;
    align-items: center;
    gap: 14px;
    font-family: "Montserrat", sans-serif;
    font-weight: 800;
    color: var(--ink);
    letter-spacing: -1px;
  }
  .brand__dot {
    border-radius: 50%;
    background: var(--blue);
  }
  .card--front .brand {
    left: 0; right: 0; top: 128px;
    justify-content: center;
    font-size: 62px;
  }
  .card--front .brand__dot { width: 54px; height: 54px; }
  .card--back .brand {
    right: 40px; top: 152px;
    font-size: 48px;
  }
  .card--back .brand__dot { width: 44px; height: 44px; }
  .web-line {
    position: absolute;
    left: 0; right: 0; top: 282px;
    display: flex;
    justify-content: center;
    align-items: center;
    gap: 8px;
    font-family: "Open Sans", sans-serif;
    font-weight: 500;
    font-size: 12px;
    letter-spacing: 1px;
    color: var(--ink);
  }
  .web-line__dot {
    width: 8px; height: 8px;
    border-radius: 50%;
    background: var(--blue);
  }
  .person {
    position: absolute;
    left: 44px; top: 54px;
    font-family: "Montserrat", sans-serif;
    color: var(--blue);
  }
  .person__name {
    margin: 0;
    font-size: 17px;
    font-weight: 500;
    letter-spacing: 0.5px;
  }
  .person__first { color: var(--ink); }
  .person__title {
    margin: 2px 0 0;
    font-size: 10px;
    font-weight: 400;
    letter-spacing: 1px;
  }
  .contacts {
    position: absolute;
    left: 44px; top: 126px;
    margin: 0; padding: 0;
    list-style: none;
    font-family: "Open Sans", sans-serif;
    font-weight: 600;
    font-size: 12.5px;
    color: var(--ink);
  }
  .contacts__item {
    display: flex;
    align-items: center;
    gap: 14px;
    height: 30px;
    margin-bottom: 8px;
  }
  .contacts__icon {
    width: 26px; height: 26px;
    flex: none;
  }
</style>
</head>
<body>
<main class="canvas">

  <section class="card card--front" aria-label="Card front">
    <svg class="card__bands" width="640" height="366" viewBox="0 0 640 366" aria-hidden="true">
      <polygon points="0,0 640,0 640,22 0,6" fill="var(--blue)"/>
      <polygon points="0,330 640,352 640,366 0,366" fill="var(--blue)"/>
    </svg>
    <div class="brand"><span class="brand__dot"></span>Norvale</div>
    <div class="web-line"><span class="web-line__dot"></span>www.norvale.com</div>
  </section>

  <section class="card card--back" aria-label="Card back">
    <svg class="card__bands" width="640" height="366" viewBox="0 0 640 366" aria-hidden="true">
      <polygon points="0,0 640,0 640,36 0,6" fill="var(--blue)"/>
      <polygon points="0,304 640,356 640,366 0,366" fill="var(--blue)"/>
    </svg>

    <div class="person">
      <p class="person__name"><span class="person__first">MARCUS T.</span> REDDING</p>
      <p class="person__title">PRINCIPAL</p>
    </div>

    <ul class="contacts">
      <li class="contacts__item">
        <svg class="contacts__icon" viewBox="0 0 26 26" aria-hidden="true">
          <rect x="1" y="1" width="24" height="24" rx="3" fill="none" stroke="var(--blue)" stroke-width="1.6"/>
          <path d="M9 8c1-1 2 0 2.5 1l.5 1.5c.2.6-.5 1-.8 1.4.6 1.4 1.6 2.4 3 3 .4-.3.8-1 1.4-.8l1.5.5c1 .5 2 1.5 1 2.5-2 2-9-3-9.1-9.1z" fill="var(--blue)"/>
        </svg>
        305-555-0142
      </li>
      <li class="contacts__item">
        <svg class="contacts__icon" viewBox="0 0 26 26" aria-hidden="true">
          <rect x="1" y="1" width="24" height="24" rx="3" fill="none" stroke="var(--blue)" stroke-width="1.6"/>
          <rect x="6" y="8" width="14" height="10" fill="var(--blue)"/>
          <path d="M6 8l7 6 7-6" fill="none" stroke="var(--paper)" stroke-width="1.4"/>
        </svg>
        MarcusTRedding@norvale.com
      </li>
      <li class="contacts__item">
        <svg class="contacts__icon" viewBox="0 0 26 26" aria-hidden="true">
          <rect x="1" y="1" width="24" height="24" rx="3" fill="none" stroke="var(--blue)" stroke-width="1.6"/>
          <circle cx="13" cy="13" r="6" fill="var(--blue)"/>
          <path d="M7 13h12M13 7c-2.5 3-2.5 9 0 12M13 7c2.5 3 2.5 9 0 12" fill="none" stroke="var(--paper)" stroke-width="0.9"/>
        </svg>
        www.norvale.com
      </li>
    </ul>

    <div class="brand"><span class="brand__dot"></span>Norvale</div>
  </section>

</main>
</body>
</html>
```